Bright Path Academy - Personal Development business 2.0 needs a social post format design.

https://www.brightpathacademy.example

Our focus with Bright Path Academy is on developing people through knowledge and skills to improve their everyday lives.
We love simplicity, Quince design and less is more.

We are crazy about personal growth, science, design, the latest gadgets and people.

We need 4 formats for our social media posts.
1. Blogs -to pronounce a blog post
2. Workshop /training - to pronounce our workshops/trainings (both online and offline)
3. Podcast - called "Kijk eens verder". To pronounce a guest we've spoken. The host is called Berend.
4. Facts - to pronounce short facts about personal development. Invites people to read more.
The formats should include: high quality pictogram (better than the uploaded picto's), 1 of the 3 logo's in the design.
It's important that we can edit the design in Affinity Design / Affinity Photo to adjust the text in the format.

Attached you find four of our current designs, which are a poor example of how the designs should look like. These are just to show you how much lines of text (more or less) will be in the designs. So please do not make a design that looks like these ;) You have carte blanche.

Our customers are mostly women (80%). We focus on both business and casual customers.

Target Market(s)

80% woman, 20% men. We focus on both business and casual customers.

Requirements
Must have
• Less is more. Quince Design alike. Simplicity.
Aimed at the women target audience.
Designs must be edible for adjusting the text in the format.
Nice to have
• Unique concept.
The design should "breathe".
Each design can have a different color, so customers identify the specific post with specific information. For example, blog is red, workshop post black, etc.

```html
<!DOCTYPE html>
<html lang="nl">
<head>
<meta charset="utf-8">
<title>Bright Path Academy – social post formats</title>
<link rel="stylesheet" href="https://fonts.googleapis.com/css2?family=Montserrat:wght@500;600;700;800;900&display=swap">
<style>
  :root{
    --board:#5e5e5e;
    --paper:#eef3fa;
    --ink:#1d1d1f;
    --white:#ffffff;
    --training:#000000;
    --podcast:#4f94d4;
    --blog:#f39208;
    --facts:#2a8011;
  }
  html,body{margin:0;padding:0;overflow:hidden;}
  body{width:1200px;height:857px;background:var(--board);position:relative;font-family:"Montserrat",sans-serif;}
  .post{position:absolute;width:350px;height:350px;background:var(--paper);overflow:hidden;color:var(--white);}
  .post--training{left:231px;top:61px;--accent:var(--training);}
  .post--podcast{left:619px;top:61px;--accent:var(--podcast);}
  .post--blog{left:231px;top:434px;--accent:var(--blog);}
  .post--facts{left:619px;top:446px;--accent:var(--facts);}
  .post__art{position:absolute;inset:0;width:350px;height:350px;}
  .accent{fill:var(--accent);}
  .badge{position:absolute;left:0;top:10px;box-sizing:border-box;height:38px;padding:0 0 0 7px;border-radius:0 19px 19px 0;background:var(--accent);display:flex;align-items:center;gap:5px;font-weight:700;font-size:10.5px;letter-spacing:.2px;text-transform:uppercase;white-space:nowrap;}
  .badge svg{flex:0 0 auto;width:22px;height:22px;fill:none;stroke:var(--white);stroke-width:1.8;stroke-linecap:round;stroke-linejoin:round;}
  .post--training .badge{width:145px;}
  .post--podcast .badge{width:96px;}
  .post--blog .badge{width:99px;padding-left:16px;}
  .post--facts .badge{width:99px;}
  .headline{position:absolute;left:10px;margin:0;font-weight:800;}
  .post--training .headline{top:196px;font-size:29px;line-height:37px;font-weight:900;}
  .post--training .meta{position:absolute;left:12px;top:267px;margin:0;font-size:14px;line-height:18px;font-weight:500;}
  .post--podcast .kicker{position:absolute;left:13px;top:186px;margin:0;font-size:23px;line-height:29px;font-weight:500;}
  .post--podcast .headline{left:8px;top:244px;font-size:32px;line-height:40px;font-weight:900;}
  .post--blog .headline{left:8px;top:183px;font-size:22px;line-height:28px;}
  .post--facts .headline{left:8px;top:200px;font-size:17.5px;line-height:22px;}
  .brand{position:absolute;right:11px;bottom:12px;margin:0;font-size:8.5px;font-weight:700;color:var(--ink);letter-spacing:.1px;}
</style>
</head>
<body>
<main class="board">

  <article class="post post--training">
    <svg class="post__art" viewBox="0 0 664 664">
      <path class="accent" d="M440,0 L664,0 L664,540 Q630,585 580,570 L262,258 Q225,218 262,178 Z"/>
      <path d="M472,0 L664,0 L664,520 Q636,560 596,548 L284,244 Q258,218 284,192 Z" fill="#c9ccd0" role="img" aria-label="Photo: smiling man in a white shirt with arms crossed in an office"/>
      <path class="accent" d="M0,298 L75,223 Q111,187 147,223 L403,479 Q425,501 403,523 L262,664 L0,664 Z"/>
    </svg>
    <div class="badge">
      <svg viewBox="0 0 24 24"><rect x="3" y="3" width="18" height="12" rx="1.5"/><circle cx="9" cy="8" r="2"/><path d="M6 14c0-2 1.5-3 3-3s3 1 3 3M14 7l4 3M3 20h18M7 20v-2M12 20v-2M17 20v-2"/></svg>
      Online Training
    </div>
    <h2 class="headline">Pre-New<br>Year’s Eve</h2>
    <p class="meta">Dinsdag 29 December,<br>19-21u</p>
    <p class="brand">Bright Path Academy</p>
  </article>

  <article class="post post--podcast">
    <svg class="post__art" viewBox="0 0 664 664">
      <path class="accent" d="M440,0 L664,0 L664,540 Q630,585 580,570 L262,258 Q225,218 262,178 Z"/>
      <path d="M472,0 L664,0 L664,520 Q636,560 596,548 L284,244 Q258,218 284,192 Z" fill="#c9ccd0" role="img" aria-label="Photo: podcast guest, smiling man in a white shirt"/>
      <path class="accent" d="M0,298 L75,223 Q111,187 147,223 L403,479 Q425,501 403,523 L262,664 L0,664 Z"/>
    </svg>
    <div class="badge">
      <svg viewBox="0 0 24 24"><circle cx="12" cy="10" r="8"/><circle cx="12" cy="10" r="4"/><path d="M12 13v8"/></svg>
      Podcast
    </div>
    <p class="kicker">Kijk eens<br>verder met</p>
    <h2 class="headline">Lotte van<br>Dijk</h2>
    <p class="brand">Bright Path Academy</p>
  </article>

  <article class="post post--blog">
    <svg class="post__art" viewBox="0 0 664 664">
      <path class="accent" d="M440,0 L664,0 L664,540 Q630,585 580,570 L262,258 Q225,218 262,178 Z"/>
      <path d="M472,0 L664,0 L664,520 Q636,560 596,548 L284,244 Q258,218 284,192 Z" fill="#cfc7bd" role="img" aria-label="Photo: woman with glasses holding a tablet"/>
      <path class="accent" d="M0,298 L75,223 Q111,187 147,223 L403,479 Q425,501 403,523 L262,664 L0,664 Z"/>
    </svg>
    <div class="badge">
      <svg viewBox="0 0 24 24"><path d="M6 4v12a4 4 0 1 0 4-4H8M12 5a7 7 0 0 1 7 7M12 1a11 11 0 0 1 11 11"/></svg>
      Blog
    </div>
    <h2 class="headline">Goede<br>voornemens<br>die je volhoudt<br>3 tips</h2>
    <p class="brand">Bright Path Academy</p>
  </article>

  <article class="post post--facts">
    <svg class="post__art" viewBox="0 0 664 664">
      <path class="accent" d="M440,0 L664,0 L664,540 Q630,585 580,570 L262,258 Q225,218 262,178 Z"/>
      <path d="M472,0 L664,0 L664,520 Q636,560 596,548 L284,244 Q258,218 284,192 Z" fill="#cfc7bd" role="img" aria-label="Photo: woman with glasses holding a tablet"/>
      <path class="accent" d="M0,298 L75,223 Q111,187 147,223 L403,479 Q425,501 403,523 L262,664 L0,664 Z"/>
    </svg>
    <div class="badge">
      <svg viewBox="0 0 24 24"><path d="M12 21a9 9 0 1 0-7-3.4L6 22l4-1.2"/><path d="M7 10h2l3-2.5v9L9 14H7z"/><path d="M15 9.5a3 3 0 0 1 0 5M17 8a5 5 0 0 1 0 8"/></svg>
      Facts
    </div>
    <h2 class="headline">“Gemiddeld haalt<br>slechts 20%<br>zijn/haar goede<br>voornemens”</h2>
    <p class="brand">Bright Path Academy</p>
  </article>

</main>
</body>
</html>
```